Tolbek cards

I want a simple business card that pops.
Logo on one side.
On side two i want.
"Are you thinking about a new building on your property, or renovating an existing structure? Contact".....
Owners Name: Dale Whitacre
Owners Phone number: 610-555-0187
Address:4076 Copper Ridge RD, Alder Falls, VT 05999
Committed to Quality, Service, and Integrity

```html
<!DOCTYPE html>
<html lang="en">
<head>
<meta charset="utf-8">
<title>Tolbek Builders LLC – Business Card</title>
<link href="https://fonts.googleapis.com/css2?family=Poppins:wght@300;400;500;600;700&display=swap" rel="stylesheet">
<style>
  :root {
    --page-bg: #f2f2f2;
    --card-white: #ffffff;
    --brown-dark: #422e1e;
    --brown-deep: #533720;
    --brown-light: #a08c74;
    --text-dark: #1c1c1c;
    --text-light: #ffffff;
  }
  * { margin: 0; padding: 0; box-sizing: border-box; }
  html, body {
    width: 1200px; height: 990px; overflow: hidden;
    background: var(--page-bg);
    font-family: "Poppins", sans-serif;
  }
  .canvas { position: relative; width: 1200px; height: 990px; }

  .card {
    position: absolute; left: 244px; width: 712px; height: 406px;
    border-radius: 48px; overflow: hidden;
    background: var(--card-white);
    box-shadow: 0 10px 28px rgba(0,0,0,0.28);
  }
  .card-front { top: 68px; }
  .card-back { top: 516px; }

  /* Front */
  .brand-lockup {
    position: absolute; left: 0; right: 0; top: 212px;
    display: flex; flex-direction: column; align-items: center;
    color: var(--brown-dark); font-weight: 700; text-align: center;
  }
  .brand-name { font-size: 80px; line-height: 1; letter-spacing: 3px; text-transform: uppercase; }
  .brand-sub { font-size: 27px; line-height: 1; letter-spacing: 2px; margin-top: 10px; text-transform: uppercase; }

  /* Back */
  .side-band {
    position: absolute; left: 0; top: 0; width: 133px; height: 100%;
    background: var(--brown-dark);
  }
  .side-brand {
    position: absolute; left: 114px; top: 44px; width: 330px;
    transform-origin: 0 0;
    transform: rotate(90deg);
    color: var(--text-light); font-weight: 700; text-align: left;
  }
  .side-brand .brand-name { font-size: 78px; letter-spacing: 2px; line-height: 0.95; }
  .side-brand .brand-sub { font-size: 26px; letter-spacing: 1px; margin-top: 4px; margin-left: 46px; }

  .contact-band {
    position: absolute; left: 133px; top: 0; right: 0; height: 171px;
    background: linear-gradient(90deg, var(--brown-light) 0%, var(--brown-deep) 100%);
    color: var(--text-light); text-align: right;
  }
  .owner-name { position: absolute; right: 30px; top: 22px; font-size: 35px; font-weight: 600; line-height: 1; letter-spacing: 0.5px; }
  .owner-role { position: absolute; right: 30px; top: 60px; font-size: 18px; font-weight: 400; line-height: 1; letter-spacing: 0.5px; }
  .contact-line {
    position: absolute; right: 26px; display: flex; align-items: center; gap: 10px;
    font-size: 18px; font-weight: 300; line-height: 1; letter-spacing: 0.4px;
  }
  .contact-phone { top: 101px; }
  .contact-address { top: 130px; }
  .icon {
    width: 23px; height: 23px; border-radius: 50%; background: var(--text-light);
    display: flex; align-items: center; justify-content: center;
  }
  .icon svg { width: 14px; height: 14px; }

  .message {
    position: absolute; right: 30px; color: var(--text-dark);
    text-align: right; font-size: 19px; line-height: 24px; font-weight: 400; letter-spacing: 0.3px;
  }
  .tagline { top: 234px; }
  .pitch { top: 305px; }
</style>
</head>
<body>
<div class="canvas">

  <section class="card card-front">
    <div class="brand-lockup">
      <div class="brand-name">Tolbek</div>
      <div class="brand-sub">Builders LLC</div>
    </div>
  </section>

  <section class="card card-back">
    <div class="side-band">
      <div class="side-brand">
        <div class="brand-name">Tolbek</div>
        <div class="brand-sub">Builders LLC</div>
      </div>
    </div>

    <div class="contact-band">
      <div class="owner-name">Dale Whitacre</div>
      <div class="owner-role">Owners</div>
      <div class="contact-line contact-phone">
        <span>610-555-0187</span>
        <span class="icon">
          <svg viewBox="0 0 24 24" aria-hidden="true"><path fill="#533720" d="M6.6 10.8a15.1 15.1 0 0 0 6.6 6.6l2.2-2.2a1 1 0 0 1 1-.25 11.4 11.4 0 0 0 3.6.57 1 1 0 0 1 1 1V20a1 1 0 0 1-1 1A17 17 0 0 1 3 4a1 1 0 0 1 1-1h3.5a1 1 0 0 1 1 1c0 1.25.2 2.45.57 3.57a1 1 0 0 1-.25 1z"/></svg>
        </span>
      </div>
      <div class="contact-line contact-address">
        <span>4076 Copper Ridge RD, Alder Falls, VT 05999</span>
        <span class="icon">
          <svg viewBox="0 0 24 24" aria-hidden="true"><path fill="#533720" d="M12 2a7 7 0 0 0-7 7c0 5.2 7 13 7 13s7-7.8 7-13a7 7 0 0 0-7-7zm0 9.5A2.5 2.5 0 1 1 12 6.5a2.5 2.5 0 0 1 0 5z"/></svg>
        </span>
      </div>
    </div>

    <p class="message tagline">Committed to Quality,<br>Service, and Integrity</p>
    <p class="message pitch">"Are you thinking about a new building<br>on your property, or renovating an<br>existing structure? Contact".....</p>
  </section>

</div>
</body>
</html>
```